Redesign of business card for Cedar Ridge Mechanical

We are looking for a new design for our business cards for Cedar Ridge Mechanical. We are a plumbing & HVAC construction company, operating on the West Coast of Canada and USA. Logo attached.
Industry/Entity Type
Construction - Plumbing & HVAC
Contact Information for Business Card
Name, address, phone numbers, email, website address
Look and feel
Each slider illustrates characteristics of the customer's brand and the style your logo design should communicate.

```html
<!DOCTYPE html>
<html lang="en">
<head>
<meta charset="utf-8">
<title>Cedar Ridge Mechanical – Business Card</title>
<link rel="stylesheet" href="https://fonts.googleapis.com/css2?family=Oswald:wght@500&family=Open+Sans:wght@400;700&display=swap">
<style>
  :root {
    --backdrop: #c9c9c9;
    --card-black: #000000;
    --card-dark: #1e1e1e;
    --paper: #ffffff;
    --ring-grey: #8a8a8a;
    --ink: #111111;
    --text-light: #ffffff;
  }
  * { margin: 0; padding: 0; box-sizing: border-box; }
  html, body {
    width: 1200px; height: 896px; overflow: hidden;
    background: var(--backdrop);
  }
  .stage { position: relative; width: 1200px; height: 896px; }
  .card {
    position: absolute; left: 334px; width: 528px; height: 300px;
    border-radius: 22px; overflow: hidden;
  }
  .card-front { top: 126px; background: var(--card-black); }
  .card-back { top: 475px; background: var(--card-dark); }

  .brand-name {
    font-family: "Oswald", sans-serif; font-weight: 500;
    text-transform: uppercase; letter-spacing: 1px; line-height: 1.05;
    text-align: center;
  }
  .card-front .brand-name {
    position: absolute; left: 0; right: 0; top: 96px;
    color: var(--text-light); font-size: 44px;
  }
  .back-art { position: absolute; inset: 0; }
  .card-back .brand-name {
    position: absolute; left: 232px; width: 290px; top: 108px;
    color: var(--ink); font-size: 34px;
  }
  .person {
    position: absolute; left: 24px; top: 52px;
    font-family: "Open Sans", sans-serif; color: var(--text-light);
  }
  .person-name { font-weight: 700; font-size: 17px; letter-spacing: .3px; }
  .person-role { font-size: 12px; margin-top: 1px; margin-left: 1px; }
  .address {
    position: absolute; left: 22px; top: 120px;
    font-family: "Open Sans", sans-serif; font-size: 14px; line-height: 19px;
    color: var(--text-light);
  }
  .contacts {
    position: absolute; left: 22px; top: 187px; list-style: none;
    font-family: "Open Sans", sans-serif; font-size: 14px; line-height: 19px;
    color: var(--text-light);
  }
  .contacts li { display: flex; align-items: center; gap: 6px; }
  .contacts svg { width: 12px; height: 12px; fill: var(--text-light); }
</style>
</head>
<body>
<div class="stage">
  <section class="card card-front">
    <div class="brand-name">Cedar Ridge<br>Mechanical</div>
  </section>

  <section class="card card-back">
    <svg class="back-art" viewBox="0 0 528 300" aria-hidden="true">
      <circle cx="402" cy="151" r="182" fill="var(--paper)"/>
      <circle cx="402" cy="151" r="178" fill="var(--ring-grey)"/>
      <circle cx="411" cy="151" r="178" fill="var(--paper)"/>
    </svg>

    <div class="person">
      <div class="person-name">DANIEL HAYES</div>
      <div class="person-role">Managing Director</div>
    </div>

    <div class="address">Your address, City<br>State, Zip 1234</div>

    <ul class="contacts">
      <li><svg viewBox="0 0 24 24"><path d="M6.6 10.8a15 15 0 0 0 6.6 6.6l2.2-2.2c.3-.3.7-.4 1-.2 1.1.4 2.3.6 3.6.6.6 0 1 .4 1 1V20c0 .6-.4 1-1 1A17 17 0 0 1 3 4c0-.6.4-1 1-1h3.5c.6 0 1 .4 1 1 0 1.3.2 2.5.6 3.6.1.3 0 .7-.2 1z"/></svg>123 456 789</li>
      <li><svg viewBox="0 0 24 24"><path d="M2 5h20v14H2zm2 2v.5l8 5 8-5V7zm0 2.8V17h16V9.8l-8 5z"/></svg>info@yourgmail.com</li>
      <li><svg viewBox="0 0 24 24"><path d="M12 2a10 10 0 1 0 0 20 10 10 0 0 0 0-20zm0 2c1 0 2.3 2 2.8 5H9.2C9.7 6 11 4 12 4zM4.3 11h4.6a20 20 0 0 0 0 2H4.3a8 8 0 0 1 0-2zm10.8 0h4.6a8 8 0 0 1 0 2h-4.6a20 20 0 0 0 0-2zM9.2 15h5.6c-.5 3-1.8 5-2.8 5s-2.3-2-2.8-5z"/></svg>www.yourwebsite.com</li>
    </ul>

    <div class="brand-name">Cedar Ridge<br>Mechanical</div>
  </section>
</div>
</body>
</html>
```